PPE EQIUPMENT

WE WOULD LIKE TO PRODUCE 2 DIFFERENT BANNERS TO BE PLACED OUTSIDE OF OUR WAREHOUSE TO ADVERTISE THAT WE HAVE FACE MASKS, HAND SANITISERS, DISINFECTANT SPRAY, FACE SHIELDS AND HAND SOAP. THE SIZE OF EACH BANNER WILL BE , portrait to be (W) 140 cm x (H) 250 cm, with 4 x eyelets. THE BANNER IS TO STATE PPE EQUIPMENT AVAILABLE HERE AND SHOW OUR PHONE NUMBER 0208-417-2953. FINALLY WE WILL REQUIRE SOME IMAGES OF THE PRODUCTS IF YOU CAN SUPPLY THESE. THANKS

```html
<!DOCTYPE html>
<html lang="en">
<head>
<meta charset="utf-8">
<title>PPE Equipment Banner</title>
<link rel="stylesheet" href="https://fonts.googleapis.com/css2?family=Anton&family=Bebas+Neue&family=Russo+One&family=Barlow:wght@300;500&family=Inter:wght@300&display=swap">
<style>
  :root {
    --page: #d6d6d6;
    --banner: #1f3a6e;
    --ink: #ffffff;
    --rule: rgba(255, 255, 255, 0.35);
    --tile: #ffffff;
  }
  * { box-sizing: border-box; margin: 0; padding: 0; }
  html, body {
    width: 960px;
    height: 1200px;
    overflow: hidden;
    background: var(--page);
  }
  .banner {
    position: absolute;
    left: 145px;
    top: 0;
    width: 670px;
    height: 1200px;
    background: var(--banner);
    color: var(--ink);
  }
  .headline {
    position: absolute;
    left: 0; right: 0;
    top: 52px;
    text-align: center;
    font-family: "Anton", sans-serif;
    font-size: 100px;
    line-height: 1;
    letter-spacing: -1px;
  }
  .subline {
    position: absolute;
    left: 0; right: 0;
    top: 166px;
    text-align: center;
    font-family: "Inter", sans-serif;
    font-weight: 300;
    font-size: 50px;
    line-height: 1;
    letter-spacing: 1px;
  }
  .rule {
    position: absolute;
    left: 54px;
    width: 567px;
    height: 1px;
    background: var(--rule);
  }
  .rule--top { top: 245px; }
  .rule--mid { top: 346px; }
  .rule--bottom { top: 1024px; }
  .phone {
    position: absolute;
    left: 0; right: 0;
    top: 258px;
    text-align: center;
    font-family: "Russo One", sans-serif;
    font-size: 70px;
    line-height: 1;
    letter-spacing: 1px;
  }
  .products {
    position: absolute;
    left: 41px;
    top: 377px;
    list-style: none;
  }
  .product {
    display: flex;
    align-items: center;
    height: 111px;
    margin-bottom: 15px;
  }
  .product__icon {
    width: 147px;
    height: 111px;
    border-radius: 8px;
    background: var(--tile);
    flex: none;
  }
  .product__name {
    margin-left: 18px;
    margin-top: -8px;
    font-family: "Bebas Neue", sans-serif;
    font-size: 68px;
    line-height: 1;
    letter-spacing: -0.5px;
  }
  .company {
    position: absolute;
    left: 0; right: 0;
    top: 1048px;
    text-align: center;
    font-family: "Barlow", sans-serif;
    font-weight: 500;
    font-size: 58px;
    line-height: 1;
    letter-spacing: 2px;
  }
  .company-line {
    position: absolute;
    left: 0; right: 0;
    top: 1118px;
    text-align: center;
    font-family: "Barlow", sans-serif;
    font-weight: 300;
    font-size: 36px;
    line-height: 1;
    letter-spacing: 2px;
  }
</style>
</head>
<body>
  <main class="banner">
    <h1 class="headline">PPE EQUIPMENT</h1>
    <p class="subline">AVAILABLE HERE</p>
    <div class="rule rule--top"></div>
    <p class="phone">0208-417-2953</p>
    <div class="rule rule--mid"></div>
    <ul class="products">
      <li class="product">
        <div class="product__icon" role="img" aria-label="Face mask pictogram"></div>
        <span class="product__name">FACE MASKS</span>
      </li>
      <li class="product">
        <div class="product__icon" role="img" aria-label="Hands under a sanitiser pump bottle pictogram"></div>
        <span class="product__name">HAND SANITISERS</span>
      </li>
      <li class="product">
        <div class="product__icon" role="img" aria-label="Disinfectant spray bottle pictogram"></div>
        <span class="product__name">DISINFECTANT SPRAY</span>
      </li>
      <li class="product">
        <div class="product__icon" role="img" aria-label="Face shield pictogram"></div>
        <span class="product__name">FACE SHIELDS</span>
      </li>
      <li class="product">
        <div class="product__icon" role="img" aria-label="Hand holding a bar of soap pictogram"></div>
        <span class="product__name">HAND SOAP</span>
      </li>
    </ul>
    <div class="rule rule--bottom"></div>
    <p class="company">HARTWELL SUPPLY CO</p>
    <p class="company-line">WAREHOUSE TRADE STOCKIST</p>
  </main>
</body>
</html>
```